Vornel Wellness Business Card

A Double Sided Business Card

I am a private company in Melbourne, Australia, working in the Health industry. I am a nutritionist and lifestyle coach, whom specialises in using raw foods ie. fruits/nuts/vegetables to help heal my clients and enable them to achieve their ultimate state of health.

I want a sophisticated design and colour for my card that appeals to both men and women from teenage through to elderly.

Front of Card:

Red apple peel spiral in the shape of an apple. I would like a leaf/leaves coming off the stem of the apple. Please see attachments for example.

***On Right Hand side of Image is business Name: Vornel Wellness

Underneath LOGO use slogan " Let Food Be Your Medicine"

***Use Deep Red and Blues for Text Colouring

Back of Card:

Marisol Dekkert
Nutritional Specialist and Lifestyle Coach

Specialising in: Diseased Conditions
Weight Management
Achieving your Ultimate State of Health

enquiries@vornelwellness.com.au 0457 396 504

**Make sure the front design of the card flows onto the back.
Updates

Email address has been amended, Also more specific details have been given for apple peel Image, and another image attached as example of Leaf on stem of apple.

I little more insight into what sort of feel were trying to create. We're apart of the health industry, and we want the card to have a medical/clinical feeling about it.

Target Market(s)

Males and Females from teenages to elderly

Industry/Entity Type

Business

Requirements
Must have
• Red Apple Peel Spiral, in the shape of an apple, with a leaf/leaves attached to stem.
***Must be in the shape of an apple
***Please use coloring on inside of apple peel to resemble inside of an apple.
Nice to have
• I would like my card to have a clinical feel.
Should not have
• We don't want the image of the apple to look like a Christmas decoration

```html
<!DOCTYPE html>
<html lang="en">
<head>
<meta charset="utf-8">
<title>Vornel Wellness Business Card</title>
<link rel="stylesheet" href="https://fonts.googleapis.com/css2?family=Quicksand:wght@500;600;700&display=swap">
<style>
  :root {
    --canvas-bg: #e9eaec;
    --card-bg: #ffffff;
    --apple-red: #d42a2a;
    --deep-navy: #25236b;
    --brand-blue: #3b4fa8;
    --ink: #1d1d2b;
    --soft-shadow: rgba(20, 20, 30, 0.18);
  }
  * { box-sizing: border-box; margin: 0; padding: 0; }
  html, body {
    width: 1200px;
    height: 900px;
    overflow: hidden;
    background: var(--canvas-bg);
    font-family: "Quicksand", sans-serif;
  }
  .sheet {
    width: 1200px;
    height: 900px;
    display: flex;
    flex-direction: column;
    align-items: center;
    justify-content: center;
    gap: 40px;
  }
  .card {
    width: 640px;
    height: 390px;
    background: var(--card-bg);
    box-shadow: 0 6px 20px var(--soft-shadow);
    position: relative;
  }

  /* Back of card */
  .card-back { color: var(--deep-navy); }
  .card-back .person {
    position: absolute;
    top: 58px;
    left: 0;
    right: 0;
    text-align: center;
  }
  .person-name {
    color: var(--apple-red);
    font-size: 34px;
    font-weight: 500;
    letter-spacing: 0.5px;
  }
  .person-role {
    font-size: 20px;
    font-weight: 600;
    line-height: 1.15;
  }
  .specialties {
    margin-top: 22px;
    color: var(--ink);
  }
  .specialties-title {
    font-size: 22px;
    font-weight: 600;
    color: var(--deep-navy);
  }
  .specialties-title .accent { color: var(--brand-blue); }
  .specialties-list {
    list-style: none;
    font-size: 18px;
    font-weight: 500;
    line-height: 1.3;
  }
  .contact {
    position: absolute;
    left: 46px;
    bottom: 40px;
    list-style: none;
    font-size: 18px;
    font-weight: 500;
    color: var(--deep-navy);
  }
  .contact li {
    display: flex;
    align-items: center;
    gap: 10px;
    margin-top: 6px;
  }
  .contact-icon { width: 24px; height: 24px; flex: none; }
  .contact-phone { font-size: 21px; }
  .back-mark {
    position: absolute;
    right: 40px;
    bottom: 62px;
    width: 58px;
    height: 58px;
    border-radius: 50%;
    background: var(--apple-red);
  }

  /* Front of card */
  .card-front {
    display: flex;
    align-items: center;
    justify-content: center;
  }
  .brand {
    display: flex;
    align-items: center;
    gap: 26px;
  }
  .brand-dot {
    width: 130px;
    height: 130px;
    border-radius: 50%;
    background: var(--apple-red);
    flex: none;
  }
  .brand-text { display: flex; flex-direction: column; }
  .brand-name {
    font-size: 50px;
    font-weight: 600;
    color: var(--brand-blue);
    line-height: 1;
  }
  .brand-slogan {
    margin-top: 8px;
    font-size: 22px;
    font-weight: 500;
    color: var(--brand-blue);
  }
</style>
</head>
<body>
<main class="sheet">
  <section class="card card-back" aria-label="Back of business card">
    <div class="person">
      <h1 class="person-name">Marisol Dekkert</h1>
      <p class="person-role">Nutritional Specialist</p>
      <p class="person-role">Lifestyle Coach</p>
      <div class="specialties">
        <h2 class="specialties-title">Speci<span class="accent">alising in:</span></h2>
        <ul class="specialties-list">
          <li>·Diseased Conditions ·Weight Management</li>
          <li>·Achieving your Ultimate State of Health</li>
        </ul>
      </div>
    </div>
    <ul class="contact">
      <li>
        <svg class="contact-icon" viewBox="0 0 24 24" aria-hidden="true">
          <circle cx="12" cy="12" r="12" fill="var(--apple-red)"/>
          <circle cx="12" cy="12" r="6.5" fill="none" stroke="#fff" stroke-width="1.4"/>
          <ellipse cx="12" cy="12" rx="2.8" ry="6.5" fill="none" stroke="#fff" stroke-width="1.2"/>
          <line x1="5.5" y1="12" x2="18.5" y2="12" stroke="#fff" stroke-width="1.2"/>
        </svg>
        <span>enquiries@vornelwellness.com.au</span>
      </li>
      <li>
        <svg class="contact-icon" viewBox="0 0 24 24" aria-hidden="true">
          <circle cx="12" cy="12" r="12" fill="var(--apple-red)"/>
          <path d="M8.2 6.5l2 2.4-1.2 1.6c.8 1.8 2.1 3.1 3.9 3.9l1.6-1.2 2.4 2-1.3 1.9c-4.6-.6-8.3-4.3-8.9-8.9z" fill="#fff"/>
        </svg>
        <span class="contact-phone">0457 396 504</span>
      </li>
    </ul>
    <div class="back-mark" aria-hidden="true"></div>
  </section>

  <section class="card card-front" aria-label="Front of business card">
    <div class="brand">
      <div class="brand-dot" aria-hidden="true"></div>
      <div class="brand-text">
        <p class="brand-name">Vornel Wellness</p>
        <p class="brand-slogan">Let Food Be Your Medicine</p>
      </div>
    </div>
  </section>
</main>
</body>
</html>
```